Basic business card

use my newly created logo - and the phrases (Lower Cost of Test & Accelarated New Product Introduction) - and my new email domain / ID - use at conferences / tradeshows

Industry/Entity Type

semiconductor

Contact Information for Business Card

Daniel K Forde, Owner, communicate via Logo - Lower COT - Cost of Test, Accelerated NPI - New Product Introduction, phone +1 555 613 0946, Chandler, Arizona, USA, daniel.forde@qal-vub.com

Font styles to use
Sans Serif

Requirements
Nice to have
• re-use my logo created via Pixel Harbor last August (#7315926)

```html
<!DOCTYPE html>
<html lang="en">
<head>
<meta charset="utf-8">
<title>QAL-VUB Business Card</title>
<link href="https://fonts.googleapis.com/css2?family=Open+Sans:wght@400;600;700&display=swap" rel="stylesheet">
<style>
  :root {
    --stage: #252525;
    --card: #1f1f22;
    --green: #7dc242;
    --orange: #f7941d;
    --white: #ffffff;
    --silver: #9aa3b0;
    --slate: #5f6a7a;
  }
  * { box-sizing: border-box; margin: 0; padding: 0; }
  html, body {
    width: 1200px; height: 780px; overflow: hidden;
    background: var(--stage);
    font-family: "Open Sans", Arial, sans-serif;
  }
  .canvas { position: relative; width: 1200px; height: 780px; }
  .card {
    position: absolute; width: 540px; height: 310px;
    background: var(--card); border-radius: 18px; overflow: hidden;
    box-shadow: 0 4px 0 var(--green), 0 14px 30px rgba(0,0,0,.55);
  }
  .card--back { left: 60px; top: 50px; }
  .card--front { left: 600px; top: 410px; }

  .wordmark {
    display: flex; align-items: center; gap: 14px;
    font-weight: 600; letter-spacing: 2px;
  }
  .wordmark__square { width: 26px; height: 26px; border-radius: 3px; }
  .card--back .wordmark {
    position: absolute; inset: 0; justify-content: center;
    font-size: 58px; color: var(--silver);
  }
  .card--back .wordmark__square { background: var(--silver); width: 40px; height: 40px; }
  .card--front .wordmark {
    position: absolute; left: 34px; top: 122px;
    font-size: 38px; color: var(--slate);
  }
  .card--front .wordmark__square { background: var(--slate); }

  .divider {
    position: absolute; left: 286px; top: 62px;
    width: 2px; height: 150px; background: var(--white);
  }
  .details { position: absolute; left: 308px; top: 46px; color: var(--white); }
  .details__name { font-size: 24px; font-weight: 700; line-height: 1.1; }
  .details__first { color: var(--green); }
  .details__last { color: var(--orange); }
  .details__title { font-size: 13px; font-weight: 600; margin-top: 3px; }
  .details__address { font-size: 12px; line-height: 1.35; margin-top: 14px; }
  .contacts { list-style: none; margin-top: 14px; font-size: 12px; line-height: 1.55; }
  .contacts li { display: flex; align-items: center; gap: 8px; }
  .contacts svg { width: 12px; height: 12px; flex: none; }

  .bands { position: absolute; left: 0; bottom: 0; width: 540px; height: 90px; }
</style>
</head>
<body>
<div class="canvas">

  <section class="card card--back">
    <div class="wordmark"><span class="wordmark__square"></span>QAL-VUB</div>
  </section>

  <section class="card card--front">
    <div class="wordmark"><span class="wordmark__square"></span>QAL-VUB</div>
    <div class="divider"></div>

    <div class="details">
      <p class="details__name"><span class="details__first">Lena</span> <span class="details__last">Marsh</span></p>
      <p class="details__title">Managing Director</p>
      <p class="details__address">4810 Harbor Ridge Dr. Suite<br>310 Mesa Verde, TX 75021</p>
      <ul class="contacts">
        <li>
          <svg viewBox="0 0 24 24"><path fill="#7dc242" d="M6.6 10.8a15.5 15.5 0 0 0 6.6 6.6l2.2-2.2a1 1 0 0 1 1-.25 11.4 11.4 0 0 0 3.6.57 1 1 0 0 1 1 1V20a1 1 0 0 1-1 1A17 17 0 0 1 3 4a1 1 0 0 1 1-1h3.5a1 1 0 0 1 1 1c0 1.25.2 2.45.57 3.6a1 1 0 0 1-.25 1z"/></svg>
          (555) 204-7731
        </li>
        <li>
          <svg viewBox="0 0 24 24"><rect x="2" y="5" width="20" height="14" rx="2" fill="#7dc242"/><path d="M3 6l9 7 9-7" fill="none" stroke="#1f1f22" stroke-width="2"/></svg>
          info@qal-vub.com
        </li>
        <li>
          <svg viewBox="0 0 24 24"><circle cx="12" cy="12" r="10" fill="#7dc242"/><path d="M2 12h20M12 2c3 3 3 17 0 20M12 2c-3 3-3 17 0 20" fill="none" stroke="#1f1f22" stroke-width="1.6"/></svg>
          www.qal-vub.com
        </li>
      </ul>
    </div>

    <svg class="bands" viewBox="0 0 540 90" aria-hidden="true">
      <path fill="var(--orange)" d="M300 34 H540 V58 H340 Q326 58 316 48 Z"/>
      <path fill="var(--green)" d="M0 64 H330 Q316 62 308 56 L300 48 H0 Z"/>
      <path fill="var(--green)" d="M0 48 H300 L322 66 H0 Z"/>
    </svg>
  </section>

</div>
</body>
</html>
```